Graphic Redesign: Front page of web app for nursery schools (PSD)

Redesign the front page of a web tool used by nursery schools for bi-directional communication with parents(PSD File type)

```html
<!DOCTYPE html>
<html lang="fi">
<head>
<meta charset="utf-8">
<title>Tenavatori – Viestintätyökalu Päiväkodeille</title>
<link rel="stylesheet" href="https://fonts.googleapis.com/css2?family=Questrial&display=swap">
<style>
  :root {
    --lime-light: #dcec2e;
    --lime-mid: #b9dc22;
    --lime-dark: #98c418;
    --brand-green: #2ea42c;
    --nav-top: #a9d22a;
    --nav-bottom: #6f9c10;
    --nav-line: #d6ee7a;
    --nav-text: #ffffff;
    --tile-bg: #d3ebc8;
    --tile-edge: #f3fbef;
    --tile-text: #3e8f86;
    --panel-bg: #c9d6bd;
    --panel-edge: #f1f7ea;
    --panel-divider: #8fcf5a;
    --heading-navy: #1f3f66;
    --body-navy: #2b4a6d;
    --tab-bg: #dcefcf;
    --tab-text: #4a9c8d;
    --tagline: #5d7d55;
    --btn-register: #a9d0a0;
    --btn-login: #7fe07c;
    --photo-frame: #f4f8ee;
    --footer-text: #f4fbe0;
  }
  * { box-sizing: border-box; margin: 0; padding: 0; }
  html, body { width: 1062px; height: 1200px; overflow: hidden; }
  body {
    font-family: "Questrial", "Century Gothic", sans-serif;
    background: radial-gradient(ellipse 70% 45% at 50% 18%, var(--lime-light), var(--lime-mid) 55%, var(--lime-dark) 100%);
    position: relative;
  }
  .brand {
    position: absolute; left: 55px; top: 88px;
    font-size: 58px; color: var(--brand-green); letter-spacing: 1px;
  }
  .social { position: absolute; left: 859px; top: 109px; display: flex; gap: 9px; }
  .social span { width: 28px; height: 28px; border-radius: 5px; display: block; box-shadow: 0 1px 2px rgba(0,0,0,.25); }
  .social .s1 { background: #f39a1c; }
  .social .s2 { background: #3fb2d8; }
  .social .s3 { background: #4666a0; }
  .social .s4 { background: #eef0ea; }

  .main-nav {
    position: absolute; left: 50px; top: 158px; width: 944px; height: 47px;
    display: flex; border-radius: 6px; overflow: hidden;
    background: linear-gradient(var(--nav-top), var(--nav-bottom));
    box-shadow: 0 2px 4px rgba(60,90,0,.35);
  }
  .main-nav a {
    color: var(--nav-text); text-decoration: none; font-size: 14.5px; white-space: nowrap;
    display: flex; align-items: center; justify-content: center;
    border-right: 2px solid var(--nav-line);
  }
  .main-nav a:last-child { border-right: none; }

  .photo {
    position: absolute; border: 4px solid var(--photo-frame);
    box-shadow: 0 3px 6px rgba(0,0,0,.3);
  }
  .photo-left { left: 100px; top: 278px; width: 339px; height: 202px; background: linear-gradient(135deg, #c9a98a, #8a6a55); }
  .photo-right { left: 596px; top: 278px; width: 340px; height: 202px; background: linear-gradient(135deg, #f3f3f0, #3c6ab2 60%, #c93a32); }
  .photo-center { left: 347px; top: 319px; width: 341px; height: 203px; background: linear-gradient(135deg, #e9d9cf, #e98aa4 50%, #f2c64a); z-index: 2; }
  .slider-arrows {
    position: absolute; left: 464px; top: 509px; width: 114px; height: 33px; z-index: 3;
    display: flex; background: #b5dca0; border: 1px solid #e8f6df;
  }
  .slider-arrows svg { width: 57px; height: 31px; }
  .slider-arrows svg + svg { border-left: 1px solid #e8f6df; }

  .tagline { position: absolute; left: 0; width: 1062px; top: 560px; text-align: center; font-size: 16.5px; color: var(--tagline); }
  .tagline span { display: inline-block; margin-left: -16px; }
  .cta {
    position: absolute; top: 595px; width: 133px; height: 37px;
    display: flex; align-items: center; justify-content: center;
    color: #fff; font-size: 15px; border-radius: 2px;
    box-shadow: 0 2px 3px rgba(60,90,0,.35);
  }
  .cta-register { left: 336px; background: var(--btn-register); }
  .cta-login { left: 575px; background: var(--btn-login); }

  .feature-tile {
    position: absolute; top: 684px; width: 155px; height: 75px;
    background: var(--tile-bg); border: 2px solid var(--tile-edge);
    box-shadow: 0 1px 3px rgba(60,90,0,.3);
    text-align: center; color: var(--tile-text); font-size: 14.5px; white-space: nowrap;
  }
  .feature-tile .icon { display: block; width: 34px; height: 34px; margin: 8px auto 4px; border-radius: 3px; }

  .offer-panel {
    position: absolute; left: 100px; top: 787px; width: 833px; height: 202px;
    background: var(--panel-bg); border: 4px solid var(--panel-edge);
    box-shadow: 0 3px 6px rgba(60,90,0,.3);
  }
  .offer-panel .divider { position: absolute; left: 511px; top: 0; bottom: 0; border-left: 1px solid var(--panel-divider); }
  .offer-tab {
    position: absolute; left: 94px; top: 806px; height: 34px;
    background: var(--tab-bg); color: var(--tab-text); font-size: 19px; white-space: nowrap;
    display: flex; align-items: center; padding: 0 14px; border-radius: 3px;
    box-shadow: 0 2px 3px rgba(0,0,0,.2);
  }
  .offer-col { position: absolute; top: 852px; color: var(--body-navy); font-size: 13px; line-height: 15.3px; }
  .offer-col h3 { font-weight: normal; font-size: 14px; color: var(--heading-navy); margin-bottom: 15px; }
  .offer-col ul { list-style: none; }
  .offer-col li { padding-left: 20px; text-indent: -20px; }
  .offer-col li::before { content: ">>\00a0"; }
  .col-left { left: 152px; width: 440px; }
  .col-right { left: 658px; width: 225px; }

  .quick-link {
    position: absolute; top: 1015px; height: 54px;
    background: var(--tile-bg); border: 2px solid var(--tile-edge);
    box-shadow: 0 1px 3px rgba(60,90,0,.3);
    display: flex; align-items: center; justify-content: center; text-align: center;
    color: var(--tile-text); font-size: 15px; line-height: 17px;
  }

  .site-footer { position: absolute; left: 0; width: 1062px; top: 1095px; text-align: center; color: var(--footer-text); }
  .site-footer nav { font-size: 14px; word-spacing: 1px; }
  .site-footer nav span { margin: 0 16px; }
  .site-footer p { font-size: 10px; margin-top: 8px; }
</style>
</head>
<body>
  <div class="brand">Tenavatori</div>
  <div class="social" aria-label="Sosiaalinen media">
    <span class="s1" role="img" aria-label="Syöte"></span>
    <span class="s2" role="img" aria-label="Viestipalvelu"></span>
    <span class="s3" role="img" aria-label="Yhteisöpalvelu"></span>
    <span class="s4" role="img" aria-label="Kuvapalvelu"></span>
  </div>

  <nav class="main-nav">
    <a style="width:90px">KOTI</a>
    <a style="width:111px">PALVELUT</a>
    <a style="width:144px">REKISTOROINTI</a>
    <a style="width:205px">PAIVAKOTI KIRJAUTUMINEN</a>
    <a style="width:185px">LASTEN KIRJAUTUMINEN</a>
    <a style="width:92px">TEEMAT</a>
    <a style="width:117px">TIETOTURVA</a>
  </nav>

  <div class="photo photo-left" role="img" aria-label="Valokuva: isoisä ja lapsi leikkivät kotona"></div>
  <div class="photo photo-right" role="img" aria-label="Valokuva: kolme hymyilevää lasta"></div>
  <div class="photo photo-center" role="img" aria-label="Valokuva: vanhemmat ja tyttö piirtävät yhdessä"></div>
  <div class="slider-arrows">
    <svg viewBox="0 0 57 31"><path d="M31 9 L24 15.5 L31 22 M38 9 L31 15.5 L38 22" fill="none" stroke="#eef8e8" stroke-width="3"/></svg>
    <svg viewBox="0 0 57 31"><path d="M19 9 L26 15.5 L19 22 M26 9 L33 15.5 L26 22" fill="none" stroke="#eef8e8" stroke-width="3"/></svg>
  </div>

  <p class="tagline"><span>Tenavatori Viestintätyökalu Päiväkodeille</span></p>
  <a class="cta cta-register">REGISTER</a>
  <a class="cta cta-login">LOGIN</a>

  <div class="feature-tile" style="left:96px"><span class="icon" role="img" aria-label="Filmikuvake" style="background:#5a5046"></span>ESITTELY VIDEO</div>
  <div class="feature-tile" style="left:267px"><span class="icon" role="img" aria-label="Pelikonsolikuvake" style="background:#e6e6e6;border:2px solid #555"></span>PELIT</div>
  <div class="feature-tile" style="left:438px"><span class="icon" role="img" aria-label="Kirja äänellä -kuvake" style="background:#2e5d8a"></span>TARINAT</div>
  <div class="feature-tile" style="left:606px"><span class="icon" role="img" aria-label="Kirja ilman ääntä -kuvake" style="background:#2e5d8a"></span>TARINAT</div>
  <div class="feature-tile" style="left:775px"><span class="icon" role="img" aria-label="Muistiokuvake" style="background:#222"></span>PALVELUT</div>

  <section class="offer-panel"><div class="divider"></div></section>
  <div class="offer-tab">TENAVATORI TARJOAA</div>
  <div class="offer-col col-left">
    <h3>Sähköistä tiedotusta koteihin päiväkodilta</h3>
    <ul>
      <li>Info päiväkodilta tekstiviestillä (vanhemmat maksavat viestit)</li>
      <li>Kuukausittaisten touhujen lista</li>
      <li>Videoita lapsien esityksistä</li>
      <li>Kuvia lapsien piirustuksista</li>
    </ul>
  </div>
  <div class="offer-col col-right">
    <h3>Web-pohjainen sisältö perheille</h3>
    <ul>
      <li>Lapsi harjoittelee nimen kirjoittamista äänen avulla</li>
      <li>Äänelliset tarinat ja pelit</li>
      <li>Mahdollisuus ladata kuvia nettiin</li>
    </ul>
  </div>

  <a class="quick-link" style="left:100px;width:156px">KIRJAUDU SISAAN<br>KOTI</a>
  <a class="quick-link" style="left:270px;width:152px">KIRJAUDU SISAAN<br>PAIVAKOTI</a>
  <a class="quick-link" style="left:441px;width:155px">REKISTEROIDY</a>
  <a class="quick-link" style="left:610px;width:156px">YHTEYSTIEDOT</a>
  <a class="quick-link" style="left:780px;width:156px">KOKEILE SIVUJA</a>

  <footer class="site-footer">
    <nav>CONTACT US<span>|</span>LEGAL &amp; POLICIES<span>|</span>PRIVACY<span>|</span>PRESS<span>|</span>SITEMAP</nav>
    <p>ALL RIGHTS RESERVED 2011 © TENAVATORI</p>
  </footer>
</body>
</html>
```